Brindlemark Offers is an online marketing platform

A daily deals site for consumers a way to bring in new clients for clients and this is who the business cards are for. Industries - Food and Drink, Things To Do, Beauty and Spas, Staycations and Services.This leaflet is going to be used to get member of the public to sign up to our website

```html
<!DOCTYPE html>
<html lang="en">
<head>
<meta charset="utf-8">
<title>Brindlemark Offers – Launch Leaflet</title>
<link href="https://fonts.googleapis.com/css2?family=Montserrat:wght@600;700&family=Questrial&family=Roboto+Condensed:wght@700&family=Poppins:wght@500;600&display=swap" rel="stylesheet">
<style>
  :root {
    --blue: #1553a5;
    --blue-deep: #1a4f9e;
    --pink: #d47cb9;
    --ink: #3c3c3c;
    --grey-text: #4a4a4a;
    --panel: #efeff0;
    --page-bg: #dcdcdc;
    --white: #ffffff;
  }
  * { box-sizing: border-box; margin: 0; padding: 0; }
  html, body { width: 1200px; height: 1200px; overflow: hidden; }
  body {
    background: var(--page-bg);
    font-family: "Questrial", "Century Gothic", sans-serif;
    color: var(--ink);
    position: relative;
  }
  .leaflet {
    position: absolute;
    left: 220px; top: 62px;
    width: 764px; height: 1082px;
    background: var(--white);
    overflow: hidden;
  }
  .brand {
    position: absolute; left: 0; right: 0; top: 112px;
    text-align: center;
  }
  .brand-name {
    display: inline-flex; align-items: center; gap: 18px;
    font-family: "Montserrat", sans-serif; font-weight: 700;
    font-size: 58px; color: var(--blue); letter-spacing: -1px;
  }
  .brand-dot { width: 44px; height: 44px; border-radius: 50%; background: var(--blue); flex: none; }
  .headline-band {
    position: absolute; left: 38px; top: 271px; width: 687px; height: 101px;
    background: linear-gradient(90deg, var(--pink) 0%, #9c74b8 45%, var(--blue-deep) 100%);
    color: var(--white);
    font-family: "Roboto Condensed", sans-serif; font-weight: 700;
    text-align: center; font-size: 29px; line-height: 33px;
    padding-top: 18px;
  }
  .headline-band .line-two { font-size: 26px; }
  .phone-photo {
    position: absolute; left: 470px; top: 398px; width: 294px; height: 440px;
    background:
      radial-gradient(ellipse 55% 50% at 55% 45%, #4ec3e8 0%, #82a4e4 35%, #d38acb 60%, rgba(222,186,166,0.8) 80%, rgba(255,255,255,0) 100%);
  }
  .intro {
    position: absolute; left: 59px; top: 394px; width: 393px;
    font-size: 20px; line-height: 24px; text-align: justify;
  }
  .launch-pill {
    position: absolute; left: 125px; top: 524px; width: 280px; height: 70px;
    border-radius: 35px;
    background: linear-gradient(90deg, var(--blue-deep) 0%, #6a6fb4 55%, var(--pink) 100%);
    color: var(--white); font-family: "Poppins", sans-serif;
    text-align: center; padding-top: 7px;
  }
  .launch-pill .small { font-size: 21px; font-weight: 500; line-height: 25px; }
  .launch-pill .date { font-size: 27px; font-weight: 600; line-height: 31px; }
  .first-offers {
    position: absolute; left: 65px; top: 622px; width: 400px;
    font-size: 20px; line-height: 24px;
  }
  .register {
    position: absolute; left: 65px; top: 688px; width: 439px;
    font-size: 20px; line-height: 24px;
  }
  .register strong { font-family: "Montserrat", sans-serif; font-weight: 700; font-size: 18px; }
  .follow {
    position: absolute; left: 165px; top: 782px; height: 44px;
    display: flex; align-items: center; gap: 16px;
    font-family: "Montserrat", sans-serif;
  }
  .follow-label { font-size: 31px; font-weight: 700; color: var(--ink); margin-right: 4px; }
  .social { font-size: 16px; font-weight: 600; color: var(--blue); }
  .social-divider { width: 0; height: 42px; border-left: 2px dashed var(--ink); }
  .entry-panel {
    position: absolute; left: 38px; top: 843px; width: 687px; height: 181px;
    background: var(--panel);
  }
  .entry-heading {
    margin-top: 16px; text-align: center;
    font-family: "Poppins", sans-serif; font-weight: 600;
    font-size: 21px; line-height: 26px; color: var(--ink);
  }
  .entry-fields {
    position: absolute; left: 33px; top: 92px;
    display: grid; grid-template-columns: 259px 280px; column-gap: 85px; row-gap: 10px;
  }
  .field { display: flex; align-items: flex-end; gap: 12px; height: 28px; }
  .field-label { font-family: "Poppins", sans-serif; font-weight: 600; font-size: 21px; color: var(--ink); white-space: nowrap; }
  .field-line { flex: 1; border-bottom: 1.5px dashed var(--ink); margin-bottom: 5px; }
  .opt-out {
    position: absolute; left: 38px; top: 1043px;
    display: flex; align-items: center; gap: 10px;
    font-size: 14px; color: var(--grey-text);
  }
  .opt-out-box { width: 16px; height: 16px; border: 1.3px solid var(--grey-text); background: var(--white); flex: none; }
</style>
</head>
<body>
  <main class="leaflet">
    <header class="brand">
      <div class="brand-name"><span class="brand-dot"></span>Brindlemark Offers</div>
    </header>

    <h1 class="headline-band">
      <div>HEY YOU!&nbsp; WANT TO WIN £200 TO SPEND ON</div>
      <div class="line-two">THE BEST EXPERIENCES THESOUTH WEST HAS TO OFFER?</div>
    </h1>

    <div class="phone-photo" role="img" aria-label="Photo of a hand holding a smartphone showing an app sign-in screen"></div>

    <p class="intro">Brindlemark Offers is a brand spanking new web-site that gives you access to exciting offers across the best restaurants, hotels, spas, leisure activities and services. Pretty cool?</p>

    <div class="launch-pill">
      <div class="small">Launching on the</div>
      <div class="date">1st August 2019 -</div>
    </div>

    <p class="first-offers">Be the first to receive exclusive offers and WIN!</p>

    <p class="register">Register for free now at <strong>brindlemarkoffers.co.uk</strong> and find inspiration for places to <strong>EAT</strong>, things to <strong>DO</strong> and where to get a <strong>PAMPER</strong>.</p>

    <div class="follow">
      <span class="follow-label">Follow us :</span>
      <span class="social">Friendwall</span>
      <span class="social-divider"></span>
      <span class="social">Chirpline</span>
      <span class="social-divider"></span>
      <span class="social">Pixgram</span>
    </div>

    <section class="entry-panel">
      <h2 class="entry-heading">Complete your details below for your chance to win and be<br>the first to receive fresh fancy offers just for you.</h2>
      <div class="entry-fields">
        <div class="field"><span class="field-label">Name:</span><span class="field-line"></span></div>
        <div class="field"><span class="field-label">Mobile:</span><span class="field-line"></span></div>
        <div class="field"><span class="field-label">Email:</span><span class="field-line"></span></div>
        <div class="field"><span class="field-label">Address:</span><span class="field-line"></span></div>
      </div>
    </section>

    <div class="opt-out">
      <span class="opt-out-box"></span>
      <span>Please tick here if you would not like to receive updates on fabulous offers and new experiences.</span>
    </div>
  </main>
</body>
</html>
```